Personal Injury Lawyer Billboard

I would like a design created featuring the image of the lawyer centered in the middle of the design.
To the left of the lawyer's image it should read "INJURED?"
To the right of the lawyer's image, it should read "CALL DEAN!"
Under Call Dean, include the phone number 318-555-0187.
At the bottom of the design include the lawyers information "Dean Marlowe Accident & Injury Lawyers"
PLEASE REMOVED THE BACKGROUND IMAGERY OF THE PHOTO SUBMITTED. Also, the colors for this design should match the colors shown in the logo (navy, white and relective soft gold). Please use those color combinations in ways that best stand out.

```html
<!DOCTYPE html>
<html lang="en">
<head>
<meta charset="UTF-8">
<title>Dean Marlowe Accident &amp; Injury Lawyers – Billboard</title>
<link href="https://fonts.googleapis.com/css2?family=Playfair+Display:wght@700;900&family=Oswald:wght@500&display=swap" rel="stylesheet">
<style>
  :root {
    --navy: #0b1f4f;
    --navy-deep: #08183f;
    --white: #ffffff;
    --ink: #0a0a0a;
    --gold-light: #f1e29a;
    --gold: #d9c07a;
    --gold-deep: #c7a85c;
    --page: #eef0f3;
  }
  html, body {
    margin: 0;
    padding: 0;
    width: 1200px;
    height: 1200px;
    overflow: hidden;
    background: var(--page);
  }
  .billboard {
    position: absolute;
    left: 30px;
    top: 410px;
    width: 1140px;
    height: 380px;
    background: var(--white);
    overflow: hidden;
    box-shadow: 0 10px 30px rgba(0,0,0,0.15);
  }
  .gold-panel {
    position: absolute;
    left: 430px;
    top: 0;
    width: 710px;
    height: 380px;
    background: linear-gradient(100deg, var(--gold-light) 0%, var(--gold) 45%, var(--gold-deep) 100%);
  }
  .injury-photo {
    position: absolute;
    left: 60px;
    top: 140px;
    width: 290px;
    height: 240px;
    background: radial-gradient(ellipse at 60% 45%, #9a9a9a 0%, #cfcfcf 45%, #ffffff 80%);
  }
  .lawyer-photo {
    position: absolute;
    left: 395px;
    top: 20px;
    width: 205px;
    height: 360px;
    background: linear-gradient(180deg, #5a5560 0%, #3a3f5c 25%, #1d2659 55%, #17204f 100%);
    border-radius: 100px 100px 0 0;
  }
  .headline-left {
    position: absolute;
    z-index: 2;
    left: 30px;
    top: 70px;
    margin: 0;
    font-family: "Playfair Display", serif;
    font-weight: 900;
    font-size: 86px;
    line-height: 1;
    color: var(--navy);
    letter-spacing: -2px;
    white-space: nowrap;
    transform: scaleX(0.8);
    transform-origin: left center;
  }
  .cta {
    position: absolute;
    z-index: 2;
    left: 618px;
    top: 22px;
    margin: 0;
    font-family: "Playfair Display", serif;
    font-weight: 900;
    font-size: 92px;
    line-height: 1;
    color: var(--ink);
    white-space: nowrap;
    transform: scaleX(0.88);
    transform-origin: left center;
  }
  .cta .cta-name { color: var(--navy); }
  .phone {
    position: absolute;
    z-index: 2;
    left: 618px;
    top: 118px;
    margin: 0;
    font-family: "Playfair Display", serif;
    font-weight: 700;
    font-size: 92px;
    line-height: 1;
    font-variant-numeric: lining-nums;
    color: var(--ink);
    white-space: nowrap;
    transform: scaleX(0.84);
    transform-origin: left center;
  }
  .firm-band {
    position: absolute;
    left: 610px;
    top: 228px;
    width: 530px;
    height: 104px;
    background: var(--navy-deep);
  }
  .firm-name {
    position: absolute;
    left: 70px;
    top: 10px;
    margin: 0;
    font-family: "Playfair Display", serif;
    font-weight: 900;
    font-size: 48px;
    line-height: 1;
    color: var(--white);
    white-space: nowrap;
    transform: scaleX(0.82);
    transform-origin: left center;
  }
  .firm-rule {
    position: absolute;
    left: 70px;
    width: 330px;
    height: 2px;
    background: var(--gold);
  }
  .firm-rule.top { top: 62px; }
  .firm-rule.bottom { top: 98px; }
  .firm-tagline {
    position: absolute;
    left: 70px;
    top: 65px;
    margin: 0;
    font-family: "Oswald", sans-serif;
    font-weight: 500;
    font-size: 26px;
    line-height: 1.2;
    color: var(--white);
    white-space: nowrap;
  }
</style>
</head>
<body>
  <div class="billboard">
    <div class="gold-panel"></div>
    <div class="injury-photo" role="img" aria-label="Black and white photo of a person with an arm in a sling being examined"></div>
    <div class="lawyer-photo" role="img" aria-label="Portrait of the lawyer in a navy suit and green tie, raising a fist"></div>
    <h1 class="headline-left">INJURED?</h1>
    <p class="cta">CALL <span class="cta-name">DEAN!</span></p>
    <p class="phone">318-555-0187</p>
    <div class="firm-band">
      <p class="firm-name">DEAN MARLOWE</p>
      <div class="firm-rule top"></div>
      <p class="firm-tagline">ACCIDENT &amp; INJURY LAWYERS</p>
      <div class="firm-rule bottom"></div>
    </div>
  </div>
</body>
</html>
```